Harvest Gateway Fellowship Ministries needs a fresh new web design

We are an up and coming multicultural church that aims to bring people into a life changing encounter with God. We need a fresh and inviting website in order to increase our internet presence and make us easier to connect with.
Here are some of the basic requirements for the site:
• Clearly displayed address, service times, and contact info
• A staff profile page
• An area for a calendar with upcoming events and their details
• Social media buttons
• Group pages for the different ministries (youth, children’s church, men, etc…)
• An area for donations and eCommerce
• A resources page for assorted media (podcasts, sermons, videos, etc.…)
• An area for prayer requests.

```html
<!DOCTYPE html>
<html lang="en">
<head>
<meta charset="utf-8">
<title>Harvest Gateway Fellowship Ministries</title>
<link rel="stylesheet" href="https://fonts.googleapis.com/css2?family=Varela+Round&family=Open+Sans:wght@400;600;700&display=swap">
<style>
:root{
  --navy:#0b3d63;
  --navy-deep:#062743;
  --gold:#f0a52a;
  --gold-light:#f3cd7c;
  --gold-dark:#d9a94d;
  --sky:#2b93de;
  --orange:#f0a030;
  --ink:#444;
  --muted:#9a9a9a;
  --line:#e2e2e2;
  --foot:#f1f1f1;
  --link:#1b5b8c;
}
*{box-sizing:border-box;margin:0;padding:0}
html,body{width:1200px;height:2403px;overflow:hidden;background:#fff}
body{position:relative;font-family:"Open Sans",Arial,sans-serif;color:var(--ink)}
.abs{position:absolute}
.round{font-family:"Varela Round","Open Sans",sans-serif}

.brand{left:0;top:0;width:1200px;height:183px;display:flex;flex-direction:column;align-items:center;justify-content:center;gap:12px}
.brand-dot{width:70px;height:70px;border-radius:50%;background:var(--gold)}
.brand-name{font-family:"Varela Round",sans-serif;font-size:20px;color:var(--navy)}

.nav{left:0;top:183px;width:1200px;height:53px;background:linear-gradient(#f4d690,var(--gold-dark));display:flex;padding-left:149px}
.nav a{display:flex;align-items:center;justify-content:center;color:#fff;font-family:"Varela Round",sans-serif;font-size:15px;text-decoration:none;border-right:1px solid rgba(255,255,255,.45);text-transform:uppercase}
.nav a.active{background:var(--navy)}

.hero{left:0;top:236px;width:1200px;height:469px;background:linear-gradient(100deg,#6d5a48 0%,#a88d75 35%,#8a6b5c 60%,#5a4a48 100%)}
.hero-title{left:0;width:1200px;text-align:center;color:#fff;font-family:"Varela Round",sans-serif}
.hero-dots{left:562px;top:673px;display:flex;gap:5px}
.hero-dots span{width:16px;height:16px;border-radius:50%;background:#fff}
.hero-dots span.on{background:#111}

.welcome-title{left:0;top:750px;width:1200px;text-align:center;font-size:29px;color:#222}
.welcome-text{left:150px;top:795px;width:900px;text-align:center;font-size:12px;line-height:20px;color:var(--muted)}

.feature{top:899px;width:294px;height:125px;color:#fff;text-align:center;padding-top:24px}
.feature h3{font-family:"Varela Round",sans-serif;font-weight:400;font-size:21px;margin-bottom:6px}
.feature p{font-size:13px;line-height:21px;padding:0 30px}
.f-verse{left:139px;background:linear-gradient(#0d5a8a,var(--navy-deep))}
.f-new{left:450px;background:linear-gradient(#f6b94a,var(--orange))}
.f-donate{left:759px;background:linear-gradient(#3aa7ea,#1c7fd0)}

.divider{left:112px;top:1083px;width:981px;height:1px;background:var(--line)}

.events-title{left:112px;top:1122px;font-size:24px;color:var(--orange)}
.calendar{left:112px;top:1166px;width:237px;border-collapse:collapse;font-size:13px;text-align:center}
.cal-head{left:112px;top:1166px;width:237px;height:29px;background:var(--navy);color:#fff;font-size:13px;display:flex;align-items:center;justify-content:space-between;padding:0 10px}
.cal-grid{left:112px;top:1195px;width:237px;display:grid;grid-template-columns:repeat(7,1fr)}
.cal-grid span{height:27px;display:flex;align-items:center;justify-content:center;border:1px solid var(--line);margin:-1px 0 0 -1px;font-size:13px;color:#333}
.cal-grid span.dow{background:var(--orange);color:#fff;font-weight:600;font-size:11px;border-color:var(--orange)}
.cal-grid span.out{color:#aaa}
.cal-grid span.today{background:#222;color:#fff}
.event{left:376px;width:358px}
.event h4{font-family:"Varela Round",sans-serif;font-weight:400;font-size:17px;color:var(--link);margin-bottom:6px}
.event p{font-size:12.5px;line-height:21px;color:var(--muted)}
.event-rule{left:376px;width:358px;height:1px;background:var(--line)}

.prayer{left:780px;top:1121px;width:313px;height:306px;border:1px solid #ddd;border-radius:3px;overflow:hidden}
.prayer-head{height:56px;background:linear-gradient(#fff,#f0f0f0);border-bottom:1px solid #ddd;padding:18px 0 0 26px;font-family:"Varela Round",sans-serif;font-size:20px;color:var(--navy)}
.field{left:806px;width:269px;height:32px;border:1px solid #ddd;border-radius:2px;font-size:12px;color:#999;padding:8px 12px}
.submit{left:806px;top:1366px;width:123px;height:36px;background:var(--orange);color:#fff;font-size:12px;font-weight:700;display:flex;align-items:center;justify-content:center}

.staff{left:0;top:1459px;width:1200px;height:364px;background:linear-gradient(#0a5a8a,#03264a 70%,#021c38)}
.staff-title{left:0;top:1505px;width:1200px;text-align:center;color:#fff;font-size:29px}
.member{top:1575px;width:240px;text-align:center}
.avatar{width:86px;height:86px;border-radius:50%;background:#fff;margin:0 auto 12px;padding:5px}
.avatar div{width:100%;height:100%;border-radius:50%;background:linear-gradient(#c9a68b,#7a5a48)}
.member h5{font-weight:600;font-size:16px;color:#fff;margin-bottom:2px}
.member p{font-size:13px;line-height:21px;color:#8fb3d3}

.res-img{width:138px;height:138px;border-radius:50%}
.res-title{font-family:"Varela Round",sans-serif;font-size:23px;line-height:30px;color:#444}
.res-text{font-size:13px;line-height:21px;color:var(--muted)}
.res-tags{display:flex;gap:14px;font-size:13px;color:var(--link)}
.res-tags span::before{content:"✓";color:#aaa;margin-right:5px}

.footer{left:0;top:2103px;width:1200px;height:239px;background:linear-gradient(#fafafa,var(--foot))}
.foot-col h6{font-family:"Varela Round",sans-serif;font-weight:400;font-size:21px;color:var(--navy);margin-bottom:14px}
.foot-col p{font-size:13px;line-height:24px;color:#555}
.foot-col .strong{font-weight:600;font-size:12px;color:#555}
.foot-col .time{color:var(--navy);font-weight:600;font-size:12.5px}
.foot-col .label{font-size:11px;color:#888}
.socials{display:flex;gap:6px}
.socials span{width:24px;height:24px;border-radius:2px}
.cards{display:flex;gap:5px;margin-top:12px}
.cards span{width:40px;height:26px;border:1px solid #333;border-radius:3px;background:#fff}
.cards span.wide{width:68px}
.bottom{left:0;top:2342px;width:1200px;height:61px;background:#fff;font-size:12px;color:#555;padding:24px 0 0 150px}
</style>
</head>
<body>

<header class="abs brand">
  <div class="brand-dot"></div>
  <div class="brand-name">Harvest Gateway Fellowship Ministries</div>
</header>

<nav class="abs nav">
  <a class="active" style="width:112px" href="#">Home</a>
  <a style="width:128px" href="#">About Us</a>
  <a style="width:124px" href="#">Events</a>
  <a style="width:192px" href="#">Prayer Request</a>
  <a style="width:122px" href="#">Donate</a>
  <a style="width:99px" href="#">Staff</a>
  <a style="width:131px;border-right:0" href="#">Contact</a>
</nav>

<section class="abs hero" role="img" aria-label="Photo of a pastor reading the Bible to a smiling multicultural congregation"></section>
<h1 class="abs hero-title" style="top:414px;font-size:42px;font-weight:400">Pellentesque faucibus accumsan ultricies</h1>
<p class="abs hero-title" style="top:468px;font-size:32px">Donec convallis pede venenatis nibh</p>
<div class="abs hero-dots"><span class="on"></span><span></span><span></span><span></span></div>

<h2 class="abs welcome-title round" style="font-weight:400">Welcome to HGFM Website Mainpage</h2>
<p class="abs welcome-text">Welcome to Harvest Gateway Fellowship Ministries, a place where we can come together and fellowship. HGFM is located in Riverside, New York and we would love to have you worship with us. We believe God is doing something extraordinary through our church and would like for you to be a part. Please prayerfully consider our church as a place you would like to worship and fellowship with us as we continue to grow.</p>

<div class="abs feature f-verse"><h3>Random Bible Verse</h3><p>Set your affection on things above, not on things on the earth.</p></div>
<div class="abs feature f-new"><h3>Are You New to</h3><p>Set your affection on things above, not on things on the earth.</p></div>
<div class="abs feature f-donate"><h3>Donations and eCommerce</h3><p>Set your affection on things above, not on things on the earth.</p></div>

<div class="abs divider"></div>

<h3 class="abs events-title round" style="font-weight:400">Upcoming Events</h3>
<div class="abs cal-head"><span>◂</span><span>JULY 2014</span><span>▸</span></div>
<div class="abs cal-grid">
  <span class="dow">Su</span><span class="dow">Mo</span><span class="dow">Tu</span><span class="dow">We</span><span class="dow">Th</span><span class="dow">Fr</span><span class="dow">Sa</span>
  <span class="out">28</span><span class="out">29</span><span class="out">30</span><span class="out">31</span><span>1</span><span>2</span><span>3</span>
  <span>4</span><span>5</span><span>6</span><span>7</span><span>8</span><span>9</span><span>10</span>
  <span>11</span><span>12</span><span>13</span><span>14</span><span>15</span><span>16</span><span>17</span>
  <span>18</span><span>19</span><span class="today">20</span><span>21</span><span>22</span><span>23</span><span>24</span>
  <span>25</span><span>26</span><span>27</span><span>28</span><span>29</span><span>30</span><span class="out">1</span>
  <span class="out">2</span><span class="out">3</span><span class="out">4</span><span class="out">5</span><span class="out">6</span><span class="out">7</span><span class="out">8</span>
</div>

<div class="abs event" style="top:1163px"><h4>Cum sociis natoque penatibus</h4><p>Vivamus porttitor purus nisi eleifend libero a tempus libero lectus feugiat felis Morbi diam mauris viverra in gravida eu mattis in ante Morbi eget arcu</p></div>
<div class="abs event-rule" style="top:1264px"></div>
<div class="abs event" style="top:1272px"><h4>Suspendisse quam leo molestie</h4><p>Vivamus porttitor purus nisi eleifend libero a tempus libero</p></div>
<div class="abs event-rule" style="top:1326px"></div>
<div class="abs event" style="top:1339px"><h4>Morbi porta libero ullamcorper</h4><p>Fermentum et lorem Nunc porta convallis pede</p></div>

<aside class="abs prayer"><div class="prayer-head">Prayer Request</div></aside>
<div class="abs field" style="top:1197px">Your Name</div>
<div class="abs field" style="top:1238px">Phone no.</div>
<div class="abs field" style="top:1280px">Email address</div>
<div class="abs field" style="top:1322px">Your Prayer</div>
<div class="abs submit">SUBMIT NOW</div>

<section class="abs staff"></section>
<h3 class="abs staff-title round" style="font-weight:400">Staff Members Profile</h3>
<div class="abs member" style="left:117px"><div class="avatar"><div role="img" aria-label="Portrait of staff member"></div></div><h5>Daniel Price</h5><p>tempus libero lectus feugiat felis<br>Morbi diam mauris</p></div>
<div class="abs member" style="left:353px"><div class="avatar"><div role="img" aria-label="Portrait of staff member"></div></div><h5>Samuel Okafor</h5><p>tempus libero lectus feugiat felis<br>Morbi diam mauris</p></div>
<div class="abs member" style="left:598px"><div class="avatar"><div role="img" aria-label="Portrait of staff member"></div></div><h5>Grace Almond</h5><p>tempus libero lectus feugiat felis<br>Morbi diam mauris</p></div>
<div class="abs member" style="left:833px"><div class="avatar"><div role="img" aria-label="Portrait of staff member"></div></div><h5>Peter Lindqvist</h5><p>tempus libero lectus feugiat felis<br>Morbi diam mauris</p></div>

<div class="abs res-img" style="left:138px;top:1874px;background:radial-gradient(#c08a4a,#5a3418)" role="img" aria-label="Photo of a crucifix"></div>
<div class="abs" style="left:293px;top:1871px;width:300px">
  <h4 class="res-title" style="font-weight:400">Resources page<br>for Assorted Media</h4>
  <p class="res-text" style="margin:6px 0 10px">Ut nisi erat fermentum vel congue id euismod in elit Fusce ultricies orci ac feugiat suscipit leo</p>
  <div class="res-tags"><span>Podcasts</span><span>Sermons</span><span>Videos</span></div>
</div>
<div class="abs res-img" style="left:625px;top:1878px;background:radial-gradient(#d8cbb4,#5a4a3a)" role="img" aria-label="Photo of an open Bible"></div>
<div class="abs" style="left:780px;top:1876px;width:310px">
  <h4 class="res-title" style="font-weight:400">Group pages for the<br>Different Ministries</h4>
  <p class="res-text" style="margin:6px 0 10px">Ut nisi erat fermentum vel congue id euismod in elit Fusce ultricies orci ac feugiat suscipit leo</p>
  <div class="res-tags"><span>Youth</span><span>Childrens Church</span><span>Men</span></div>
</div>

<footer class="abs footer"></footer>
<div class="abs foot-col" style="left:147px;top:2152px">
  <h6>Quick Links</h6>
  <p class="strong">About Us<br>Upcoming Events<br>Prayer Request<br>Donate</p>
</div>
<div class="abs foot-col" style="left:346px;top:2152px">
  <h6>Contact Info</h6>
  <p>48 Orchard Lane Suite 2<br>New York<br>555.014.2260<br>hello@harvestgateway.org</p>
</div>
<div class="abs foot-col" style="left:556px;top:2152px">
  <h6>Service Timing</h6>
  <p><span class="label">Monday to Friday</span><br><span class="time">10:00 Am to 7:00 Pm</span><br><span class="label">Saturday</span><br><span class="time">10:00 Am to 2:00 Pm</span></p>
</div>
<div class="abs foot-col" style="left:777px;top:2152px">
  <h6>Connect with Us</h6>
  <div class="socials"><span style="background:#3b5a9a"></span><span style="background:#5bc0ea"></span><span style="background:#1a6fa8"></span><span style="background:#f08a24"></span></div>
  <div class="cards"><span></span><span></span><span></span><span class="wide"></span></div>
</div>

<div class="abs bottom">© 2014 Company Name&nbsp; All right reserved&nbsp; Term of Use</div>

</body>
</html>
```